Retail Jewelry Business Card Design Project

We are in need of a new business card design for a retail jewelry store. This store is in the business of fine jewelry including but not specific to bridal jewelry, diamonds, designer jewelry and watches.

This store has been in business for 20 years but continues to strive for a modern professional appeal. The main colors use for this business are a royal blue, white and silver.

Target Market(s)

Target market is ages 18-50

Industry/Entity Type

Jewelry

Requirements
Must have
• Sales Person Name
Sales Person Email Address

Store Address
Store Phone
Website

Standard business card size. No odd shapes or sizes.
Nice to have
• Overall modern feel for card.

We have thought that a design with a nice feature of the logo on the back of the card would be nice but open to ideas.
Should not have
• No specific images of jewelry should be used.

```html
<!DOCTYPE html>
<html lang="en">
<head>
<meta charset="utf-8">
<title>Warren Hale Fine Jewelry – Business Card</title>
<link rel="stylesheet" href="https://fonts.googleapis.com/css2?family=Cormorant+Garamond:ital,wght@0,600;1,700&family=Questrial&display=swap">
<style>
  :root {
    --royal: #2e3590;
    --lavender: #7a78c0;
    --white: #ffffff;
    --backdrop: #e9e9ec;
    --shadow: rgba(20, 20, 40, 0.22);
  }
  * { box-sizing: border-box; margin: 0; padding: 0; }
  html, body {
    width: 1200px; height: 750px; overflow: hidden;
    background: var(--backdrop);
  }
  .canvas { position: relative; width: 1200px; height: 750px; }
  .card {
    position: absolute; top: 220px;
    width: 540px; height: 309px;
    box-shadow: 0 8px 24px var(--shadow);
    overflow: hidden;
  }
  .card--front { left: 40px; background: var(--white); }
  .card--back { left: 620px; background: var(--royal); }

  .card__waves { position: absolute; inset: 0; width: 100%; height: 100%; }

  .brand { position: absolute; font-family: "Cormorant Garamond", serif; font-weight: 600; line-height: 1; }
  .brand__name { display: block; font-size: 50px; letter-spacing: 0.5px; }
  .brand__tag { display: block; font-size: 22px; letter-spacing: 3px; text-transform: uppercase; margin-top: 6px; }

  .card--front .brand { left: 40px; top: 40px; color: var(--royal); }
  .card--back .brand { left: 0; right: 0; top: 88px; text-align: center; color: var(--white); }
  .card--back .brand__name { font-size: 62px; }
  .card--back .brand__tag { font-size: 26px; letter-spacing: 4px; margin-top: 8px; }

  .person {
    position: absolute; left: 44px; top: 156px;
    font-family: "Cormorant Garamond", serif; font-style: italic; font-weight: 700;
    font-size: 19px; color: var(--royal); letter-spacing: 0.5px;
  }

  .contact {
    position: absolute; right: 24px; top: 98px;
    list-style: none; text-align: right;
    font-family: "Questrial", sans-serif; font-size: 12px; color: var(--white);
  }
  .contact li { display: flex; justify-content: flex-end; align-items: center; gap: 6px; height: 22px; }
  .contact svg { width: 11px; height: 11px; flex: none; }

  .address {
    position: absolute; right: 24px; top: 214px;
    font-family: "Questrial", sans-serif; font-size: 12px; color: var(--white);
  }

  .website {
    position: absolute; left: 0; right: 0; top: 232px; text-align: center;
    font-family: "Questrial", sans-serif; font-size: 14px; letter-spacing: 3px; color: var(--white);
  }
</style>
</head>
<body>
<main class="canvas">

  <section class="card card--front" aria-label="Business card front">
    <svg class="card__waves" viewBox="0 0 540 309" preserveAspectRatio="none" aria-hidden="true">
      <path d="M540,22 C470,24 392,54 318,104 C236,162 126,224 0,238 L0,309 L540,309 Z" fill="var(--lavender)"/>
      <path d="M540,40 C470,42 400,70 330,120 C250,178 140,238 0,252 L0,309 L540,309 Z" fill="var(--royal)"/>
      <path d="M0,280 C100,278 180,262 232,236" fill="none" stroke="var(--white)" stroke-width="3"/>
      <path d="M0,288 C140,287 250,280 330,258 L340,262 C260,290 150,298 0,299 Z" fill="var(--lavender)"/>
    </svg>

    <h1 class="brand">
      <span class="brand__name">Warren Hale</span>
      <span class="brand__tag">Fine Jewelry</span>
    </h1>

    <p class="person">Warren Hale Morrison</p>

    <ul class="contact">
      <li>
        <svg viewBox="0 0 12 12" aria-hidden="true"><circle cx="6" cy="6" r="5.2" fill="none" stroke="currentColor" stroke-width="1.2"/><path d="M4 3.5 L5 5 L4.6 5.6 C5 6.4 5.6 7 6.4 7.4 L7 7 L8.5 8 L7.8 8.8 C5.6 8.6 3.4 6.4 3.2 4.2 Z" fill="currentColor"/></svg>
        555-318-2046
      </li>
      <li>
        <svg viewBox="0 0 12 12" aria-hidden="true"><rect x="1" y="3" width="10" height="7" fill="currentColor"/><path d="M1 3 L6 7 L11 3" fill="none" stroke="var(--royal)" stroke-width="1"/></svg>
        warren@warrenhalejewelry.com
      </li>
      <li>
        <svg viewBox="0 0 12 12" aria-hidden="true"><circle cx="6" cy="6" r="5" fill="none" stroke="currentColor" stroke-width="1.1"/><ellipse cx="6" cy="6" rx="2.2" ry="5" fill="none" stroke="currentColor" stroke-width="1"/><path d="M1 6 H11" stroke="currentColor" stroke-width="1"/></svg>
        www.warrenhalejewelry.com
      </li>
    </ul>

    <p class="address">2280 Bayview Avenue, Harbor City, FL 32000</p>
  </section>

  <section class="card card--back" aria-label="Business card back">
    <h2 class="brand">
      <span class="brand__name">Warren Hale</span>
      <span class="brand__tag">Fine Jewelry</span>
    </h2>
    <p class="website">www.warrenhalejewelry.com</p>
  </section>

</main>
</body>
</html>
```